Unique Business Card Design

Unique Business Card design for our orthotic and prosthetic company. Our logo is on our website, color is light blue. Unique shape (artificial leg shaped, vertical, etc..) preferred. Logo, business name, individual name and basic demographics needed.

Industry/Entity Type

Business

Contact Information for Business Card

Logo, Industry, Phone # Logo, "Prosthetic & Orthotic Services" Place to add individual name and contact info

Colors
cee9f5

Requirements
Must have
• The icon must be there, placement of "Prosthetic & Orthotic Services" can be moved
Nice to have
• Like the mix of light blue, and a little darker blue. One design included the icons from my website which was a nice touch

```html
<!DOCTYPE html>
<html lang="en">
<head>
<meta charset="utf-8">
<title>Limbworks Inc. Business Card</title>
<link href="https://fonts.googleapis.com/css2?family=Arimo:wght@400;700&display=swap" rel="stylesheet">
<style>
  :root {
    --stage: #5a5a5a;
    --stage-edge: #2b2b2b;
    --brand-blue: #1f5fb0;
    --card-blue: #2a6ec0;
    --card-blue-deep: #1c57a3;
    --tint: #cee9f5;
    --white: #ffffff;
  }
  * { box-sizing: border-box; margin: 0; padding: 0; }
  html, body { width: 1200px; height: 950px; overflow: hidden; }
  body {
    font-family: "Arimo", Arial, sans-serif;
    background: radial-gradient(ellipse at 45% 40%, var(--stage) 0%, var(--stage-edge) 75%);
    position: relative;
  }
  .card {
    position: absolute;
    width: 600px;
    height: 343px;
    border-radius: 22px;
    overflow: hidden;
  }
  .card-front { left: 90px; top: 90px; background: var(--white); }
  .card-back {
    left: 510px; top: 510px;
    background: linear-gradient(160deg, var(--card-blue) 0%, var(--card-blue-deep) 100%);
    color: var(--white);
  }

  /* front lockup */
  .front-lockup { position: absolute; left: 70px; top: 118px; display: flex; align-items: center; gap: 22px; }
  .brand-dot { width: 104px; height: 104px; border-radius: 50%; background: var(--brand-blue); flex: none; }
  .brand-name { font-weight: 700; font-size: 36px; letter-spacing: 0.5px; color: var(--brand-blue); line-height: 1; }
  .brand-rule { height: 2px; background: var(--brand-blue); margin: 8px 0 7px; }
  .brand-tagline { font-size: 17px; color: var(--brand-blue); }

  /* back */
  .back-lockup { position: absolute; left: 34px; top: 40px; width: 300px; }
  .back-lockup .brand-name { color: var(--white); font-size: 30px; }
  .back-lockup .brand-rule { background: var(--white); }
  .back-lockup .brand-tagline { color: var(--white); font-size: 15px; }

  .person { position: absolute; left: 34px; top: 150px; }
  .person-name { font-weight: 700; font-size: 20px; }
  .person-title { font-weight: 700; font-size: 12px; margin-top: 3px; }

  .contact-list { position: absolute; left: 34px; top: 205px; list-style: none; font-size: 13px; }
  .contact-list li { display: flex; align-items: center; gap: 9px; height: 20px; }
  .contact-list svg { width: 13px; height: 13px; fill: var(--white); flex: none; }
  .address { position: absolute; left: 34px; top: 310px; font-size: 13px; }

  .figure-area {
    position: absolute; right: 40px; top: 30px;
    width: 160px; height: 283px; border-radius: 80px;
    background: linear-gradient(180deg, rgba(206,233,245,0.35), rgba(206,233,245,0.15));
  }
</style>
</head>
<body>

<section class="card card-front" aria-label="Card front">
  <div class="front-lockup">
    <div class="brand-dot"></div>
    <div class="brand-text">
      <div class="brand-name">LIMBWORKS INC.</div>
      <div class="brand-rule"></div>
      <div class="brand-tagline">Prosthetic &amp; Orthotic Services</div>
    </div>
  </div>
</section>

<section class="card card-back" aria-label="Card back">
  <div class="back-lockup">
    <div class="brand-name">LIMBWORKS INC.</div>
    <div class="brand-rule"></div>
    <div class="brand-tagline">Prosthetic &amp; Orthotic Services</div>
  </div>

  <div class="person">
    <div class="person-name">Miriam Talbot</div>
    <div class="person-title">CO LPO</div>
  </div>

  <ul class="contact-list">
    <li><svg viewBox="0 0 16 16"><path d="M3 1l3 3-2 2c1 2 3 4 5 5l2-2 3 3-2 3C6 14 2 10 1 3z"/></svg>555.210.4400</li>
    <li><svg viewBox="0 0 16 16"><path d="M4 0h8v16H4zM5.5 2v10h5V2z"/></svg>555.210.4419</li>
    <li><svg viewBox="0 0 16 16"><path d="M3 1h7v4H3zM1 6h14v7H1zM4 10h8v5H4z"/></svg>555-3086127</li>
    <li><svg viewBox="0 0 16 16"><path d="M0 3h16v10H0zM1.5 4.5L8 9l6.5-4.5z"/></svg>mtalbot@limbworksinc.com</li>
    <li><svg viewBox="0 0 16 16"><circle cx="8" cy="8" r="7.5"/></svg>www.limbworksinc.com</li>
  </ul>
  <div class="address">2310 Harbor Ave., Fairview, NY 10000</div>

  <div class="figure-area" role="img" aria-label="Large brand emblem area"></div>
</section>

</body>
</html>
```